Business Card Design

We are a commercial real estate brokerage in San Francisco, leasing office buildings downtown.
I would like a clean, elegant look. Simple but powerful .

Industry/Entity Type

Business

Contact Information for Business Card

Derek Holloway
lic# 07258143
415.555.0172
derek@velt-commercial.example
velt-commercial.example

```html
<!DOCTYPE html>
<html lang="en">
<head>
<meta charset="utf-8">
<title>VELT Commercial – Business Card</title>
<link rel="stylesheet" href="https://fonts.googleapis.com/css2?family=Source+Sans+3:wght@400;600&display=swap">
<style>
  :root {
    --page: #e9e9eb;
    --card: #ffffff;
    --slate: #7d8ba8;
    --slate-light: #c9d0de;
    --ink: #4a4a4f;
    --muted: #6e6e74;
    --rule: #b9b9be;
    --dark: #3c3c40;
  }
  * { box-sizing: border-box; margin: 0; padding: 0; }
  html, body { width: 1200px; height: 950px; overflow: hidden; }
  body {
    background: var(--page);
    font-family: "Source Sans 3", Arial, sans-serif;
    color: var(--ink);
    position: relative;
  }
  .card {
    position: absolute;
    left: 250px;
    width: 700px;
    height: 400px;
    background: var(--card);
    box-shadow: 0 6px 18px rgba(0,0,0,.18);
    overflow: hidden;
  }
  .card--back { top: 50px; }
  .card--front { top: 500px; }

  /* Back side */
  .brand-lockup {
    display: flex;
    align-items: center;
    justify-content: center;
    gap: 16px;
    margin-top: 130px;
  }
  .brand-mark { width: 22px; height: 22px; background: var(--slate); }
  .brand-name {
    font-weight: 600;
    font-size: 52px;
    letter-spacing: 2px;
    color: var(--slate);
    line-height: 1;
  }
  .tagline {
    margin-top: 40px;
    text-align: center;
    font-size: 17px;
    line-height: 1.35;
    color: var(--muted);
  }

  /* Front side */
  .front-art { position: absolute; inset: 0; }
  .front-brand {
    position: absolute;
    right: 44px;
    top: 70px;
    display: flex;
    align-items: center;
    gap: 12px;
  }
  .front-brand .brand-mark { width: 16px; height: 16px; }
  .front-brand .brand-name { font-size: 38px; letter-spacing: 1.5px; }
  .licence {
    position: absolute;
    right: 40px;
    top: 186px;
    font-size: 15px;
    color: var(--muted);
  }
  .website {
    position: absolute;
    right: 32px;
    top: 258px;
    font-size: 14px;
    color: #ffffff;
  }
  .person-name {
    position: absolute;
    left: 40px;
    top: 246px;
    font-size: 23px;
    font-weight: 600;
    letter-spacing: .5px;
    text-transform: uppercase;
    color: var(--slate);
  }
  .contact-list {
    position: absolute;
    left: 40px;
    top: 296px;
    list-style: none;
    font-size: 15px;
    color: var(--muted);
  }
  .contact-list li { display: flex; align-items: center; gap: 12px; height: 24px; }
  .contact-list svg { width: 14px; height: 14px; fill: var(--muted); }
</style>
</head>
<body>

<section class="card card--back" aria-label="Card back">
  <div class="brand-lockup">
    <span class="brand-mark"></span>
    <span class="brand-name">VELT COMMERCIAL</span>
  </div>
  <p class="tagline">commercial real estate brokerage in San Francisco<br>leasing office buildings downtown.</p>
</section>

<section class="card card--front" aria-label="Card front">
  <svg class="front-art" viewBox="0 0 700 400" width="700" height="400" aria-hidden="true">
    <defs>
      <linearGradient id="slateBand" x1="0" y1="0" x2="1" y2="0">
        <stop offset="0" stop-color="#eef0f4"/>
        <stop offset=".55" stop-color="#c9d0de"/>
        <stop offset="1" stop-color="#7d8ba8"/>
      </linearGradient>
    </defs>
    <line x1="250" y1="165" x2="660" y2="165" stroke="#b9b9be" stroke-width="1"/>
    <polygon points="445,248 700,248 700,350 385,350 415,282" fill="#3c3c40"/>
    <polyline points="40,283 415,283 445,248" fill="none" stroke="#b9b9be" stroke-width="1"/>
    <polygon points="0,368 360,368 385,350 700,350 700,400 0,400" fill="url(#slateBand)"/>
    <line x1="0" y1="392" x2="700" y2="392" stroke="#3c3c40" stroke-width="4"/>
  </svg>

  <div class="front-brand">
    <span class="brand-mark"></span>
    <span class="brand-name">VELT COMMERCIAL</span>
  </div>
  <p class="licence">lic# 07258143</p>
  <p class="website">www.velt-commercial.example</p>

  <h1 class="person-name">Derek Holloway</h1>
  <ul class="contact-list">
    <li>
      <svg viewBox="0 0 24 24"><path d="M6.6 10.8a15.1 15.1 0 0 0 6.6 6.6l2.2-2.2c.3-.3.7-.4 1-.2 1.1.4 2.3.6 3.6.6.6 0 1 .4 1 1V20c0 .6-.4 1-1 1A17 17 0 0 1 3 4c0-.6.4-1 1-1h3.5c.6 0 1 .4 1 1 0 1.3.2 2.5.6 3.6.1.3 0 .7-.2 1z"/></svg>
      <span>415.555.0172</span>
    </li>
    <li>
      <svg viewBox="0 0 24 24"><path d="M2 5h20v14H2z M2 5l10 8 10-8" /></svg>
      <span>derek@velt-commercial.example</span>
    </li>
  </ul>
</section>

</body>
</html>
```